RQV Wellness Co Business Card for food and Beverage Wizards & Alchemists

One main business card design for a wellness enterprise which represents two brands. We need one primary card design, for two different employees. The only difference between the cards will be the name, title and phone number for each employee, all other design elements will be same.
I've uploaded the logos for each brand. I have also uploaded a mockup which I made using Google's drawing tool. I can provide example images of business cards we find attractive if you would like some help picturing what we like.
I'm picturing the color splash on the back of the card below the two logos to be a dark burgundy or blue. This may sound a bit silly but the feel of the card and color should look almost like wizard dress robes. Dark emerald green, dark blue and dark burgundy with black undertones and gold lace.

Reason: Thank you all for the submissions. I will need some extra time to give you feedback. Cheers

Target Market(s)

Healthy food and beverage industry

Industry/Entity Type

Health And Wellness

Contact Information for Business Card

On one side we would like the business name, location, title of employee, employee name and contact details. On the flip side we would like our two brand logos and a splash of color. We would like the card to have a black font with some gold accents if possible. We would also like the trim of the business card or a middle ply within the card stock to have a color other than white.

Font styles to use
Serif

Colors
ec1f27
0255a3
00a990

Requirements
Must have
• Bold dark colors, happy to provide sample photos of business cards I like from snapgallery. Must have a version for two different employees. Must be sharp, modern and chic.
Nice to have
• Thick card stock layer in between the front and back of card that is either black or gold lace or something to make it feel, well let's say to make it feel expensive.
Should not have
• Should not have any cartoon-ey elements. All business.

```html
<!DOCTYPE html>
<html lang="en">
<head>
<meta charset="utf-8">
<title>RQV Wellness Co Business Card</title>
<link rel="stylesheet" href="https://fonts.googleapis.com/css2?family=Roboto:wght@400;500&display=swap">
<style>
  :root {
    --backdrop: #2b2b2b;
    --card-black: #1c1c1c;
    --burgundy: #6e1a22;
    --burgundy-deep: #4f1219;
    --gold: #b39a4a;
    --silver: #e8e8e8;
  }
  * { margin: 0; padding: 0; box-sizing: border-box; }
  html, body {
    width: 1200px;
    height: 1017px;
    overflow: hidden;
    background: var(--backdrop);
    font-family: "Roboto", Arial, sans-serif;
  }
  .canvas {
    position: relative;
    width: 1200px;
    height: 1017px;
    display: flex;
    align-items: center;
    justify-content: center;
    gap: 40px;
  }
  .card {
    position: relative;
    width: 540px;
    height: 309px;
    background: var(--card-black);
    overflow: hidden;
    box-shadow: 0 18px 40px rgba(0,0,0,0.45);
  }
  .card-front .color-splash {
    position: absolute;
    inset: 0;
    width: 100%;
    height: 100%;
  }
  .brand-marks {
    position: absolute;
    top: 98px;
    left: 190px;
    right: 30px;
    display: flex;
    align-items: center;
    justify-content: space-between;
  }
  .brand-name {
    display: flex;
    align-items: center;
    gap: 8px;
    font-size: 16px;
    font-weight: 500;
    letter-spacing: 0.04em;
  }
  .brand-name.guild { color: var(--silver); }
  .brand-name.wellness { color: var(--gold); }
  .brand-dot {
    width: 10px;
    height: 10px;
    border-radius: 50%;
    background: currentColor;
  }
  .contact-block {
    position: absolute;
    top: 112px;
    left: 0;
    right: 30px;
    text-align: center;
    color: var(--gold);
    line-height: 1.3;
  }
  .employee-name { font-size: 22px; font-weight: 500; }
  .employee-title { font-size: 16px; font-weight: 400; margin-bottom: 6px; }
  .employee-phone, .employee-email { font-size: 13px; font-weight: 400; }
</style>
</head>
<body>
<main class="canvas">
  <section class="card card-front" aria-label="Card front with brand names">
    <svg class="color-splash" viewBox="0 0 540 309" preserveAspectRatio="none" aria-hidden="true">
      <defs>
        <linearGradient id="splashFill" x1="0" y1="0" x2="1" y2="1">
          <stop offset="0" stop-color="#7a1d26"/>
          <stop offset="1" stop-color="#4f1219"/>
        </linearGradient>
      </defs>
      <path d="M0,38 C110,36 180,110 225,190 C255,245 285,290 300,309 L0,309 Z" fill="url(#splashFill)"/>
    </svg>
    <div class="brand-marks">
      <div class="brand-name guild"><span class="brand-dot"></span>Vale Guild</div>
      <div class="brand-name wellness">RQV Wellness Co</div>
    </div>
  </section>

  <section class="card card-back" aria-label="Card back with contact details">
    <div class="contact-block">
      <p class="employee-name">Marcus Hale</p>
      <p class="employee-title">Beverage Alchemist</p>
      <p class="employee-phone">555.201.4478</p>
      <p class="employee-email">rqvwellnessco@mailbox.com</p>
    </div>
  </section>
</main>
</body>
</html>
```